Support Welcome Packet Redesign

Looking to redesign our current "welcome packet" that we send to our new customers to help them understand our support service. It is currently in Microsoft Word and would like to remain in either word or publisher. Something that we can easily edit, as the content adjusts based on the customer needs. We want this document to be simple and understandable as it should be something our customers can reference at any time during our contract and easy to navigate.

Target Market(s)

Current Customers. Healthcare, Oil & Gas, Transportation, etc.

Industry/Entity Type

It Service

Font styles to use
Sans Serif

Requirements
Must have
• Table of Contents, inVex Logo and current content
Nice to have
• Easy navigation. Redone final page (contact info)

```html
<!DOCTYPE html>
<html lang="en">
<head>
<meta charset="utf-8">
<title>Support Information – inVex Welcome Packet</title>
<link rel="stylesheet" href="https://fonts.googleapis.com/css2?family=Carlito:wght@400;700&display=swap">
<style>
  :root{
    --orange:#f47b20;
    --orange-soft:#f9a35e;
    --ink:#1a1a1a;
    --grey-top:#e6e6e6;
    --grey-mid:#f4f4f4;
    --white:#ffffff;
    --blue:#2f8fd8;
    --yellow:#f5d31e;
    --green:#6cb33f;
  }
  html,body{margin:0;padding:0;overflow:hidden;}
  body{width:848px;height:1200px;background:var(--white);font-family:"Carlito",sans-serif;color:var(--ink);}
  .page{position:relative;width:848px;height:1200px;overflow:hidden;
    background:linear-gradient(180deg,var(--grey-top) 0px,var(--grey-mid) 200px,var(--white) 330px);}
  .header-art{position:absolute;left:0;top:0;width:848px;height:300px;}
  .page-title{position:absolute;left:80px;top:52px;margin:0;font-size:30px;font-weight:700;color:var(--white);letter-spacing:.2px;}
  .brand{position:absolute;left:690px;top:80px;width:120px;text-align:center;}
  .brand-square{display:block;width:56px;height:56px;margin:0 auto 8px;background:var(--orange);border-radius:6px;}
  .brand-name{font-size:34px;font-weight:700;color:var(--orange);line-height:1;}
  .content{position:absolute;left:80px;top:296px;width:692px;}
  .section-title{margin:0;font-size:27px;font-weight:700;color:var(--orange);line-height:1.2;}
  .section-sub{margin:2px 0 16px;font-size:16.5px;font-weight:700;}
  .team h3{margin:0 0 4px;font-size:20.5px;font-weight:400;text-decoration:underline;text-underline-offset:3px;}
  .team p{margin:0 0 16px;font-size:17.3px;line-height:24.6px;}
  .footer{position:absolute;left:52px;top:1064px;width:760px;height:30px;display:flex;align-items:center;font-size:14.5px;}
  .footer-brand{font-size:20px;font-weight:700;color:var(--orange);display:flex;align-items:center;margin-right:18px;}
  .footer-brand .dot{width:18px;height:18px;background:var(--orange);border-radius:3px;margin-right:6px;}
  .footer-item{display:flex;align-items:center;margin-right:18px;}
  .footer-item svg{margin-right:5px;}
  .color-bar{position:absolute;left:8px;top:1099px;width:840px;height:5px;
    background:linear-gradient(90deg,var(--blue) 0%,var(--blue) 22%,var(--orange) 22%,var(--orange) 43%,var(--yellow) 43%,var(--yellow) 64%,var(--green) 64%,var(--green) 100%);}
  .page-number{position:absolute;left:778px;top:1115px;font-size:20px;}
</style>
</head>
<body>
<div class="page">
  <svg class="header-art" viewBox="0 0 848 300" aria-hidden="true">
    <polygon points="0,0 492,0 600,108 0,108" fill="var(--orange)"/>
    <polyline points="564,0 756,252 848,214" fill="none" stroke="var(--orange)" stroke-width="2.5"/>
  </svg>
  <svg class="header-art" viewBox="0 0 848 300" role="img" aria-label="Decorative orange gear graphic">
    <circle cx="420" cy="108" r="95" fill="var(--orange)" opacity=".9"/>
    <circle cx="268" cy="92" r="36" fill="var(--orange-soft)"/>
    <polygon points="0,0 492,0 600,108 0,108" fill="var(--orange)"/>
  </svg>

  <h1 class="page-title">Support Information</h1>

  <div class="brand">
    <span class="brand-square"></span>
    <div class="brand-name">inVex</div>
  </div>

  <main class="content">
    <h2 class="section-title">Support Information</h2>
    <p class="section-sub">inVex Support Teams and Escalation Path</p>

    <section class="team">
      <h3>Technical Support Team</h3>
      <p>The technical support team is your first point of contact. The support team will assist with the entry of work tickets for issues and with contacting inVex team members on your escalation path in the case of an urgent issue.</p>
    </section>
    <section class="team">
      <h3>Network Engineering Team</h3>
      <p>Our support team includes trained systems and network engineers whose responsibilities include the diagnosis and resolution of complex issues outside of the scope of support provided by the technical support team. The Network Engineering Team is the first point of escalation if the Technical Support Team cannot resolve an issue.</p>
    </section>
    <section class="team">
      <h3>Architecture/Development Team</h3>
      <p>The Architecture and Development Team provides advanced support for critical and highly complex issues.&nbsp; The Architecture/Development Team acts as the final escalation point for any issues that you may encounter in your environment.&nbsp; This team is also responsible for the design and implementation of new systems required for new work and highly complex issues.</p>
    </section>
    <section class="team">
      <h3>Management Team</h3>
      <p>The Management Team serves as the primary point of contact during the implementation or migration phase of a new project, or for any issues that are outside of the scope of the technical support team. However, once the product has moved into your production environment, primary contact should be Technical Support Services for tracking, auditing and response time purposes.</p>
    </section>
  </main>

  <footer class="footer">
    <div class="footer-brand"><span class="dot"></span>inVex Technology</div>
    <div class="footer-item">
      <svg width="14" height="18" viewBox="0 0 14 18"><path d="M7 0C3 0 0 3 0 7c0 5 7 11 7 11s7-6 7-11c0-4-3-7-7-7z" fill="var(--blue)"/><circle cx="7" cy="7" r="2.5" fill="var(--white)"/></svg>
      240 W Sample Ave&nbsp; Mesa, AZ 85210
    </div>
    <div class="footer-item">
      <svg width="16" height="16" viewBox="0 0 16 16"><path d="M3 1l3 3-2 2c1 2 3 4 5 5l2-2 3 3-2 3C6 15 1 10 0 4z" fill="var(--blue)"/></svg>
      480-555-0187
    </div>
    <div class="footer-item">
      <svg width="16" height="16" viewBox="0 0 16 16"><circle cx="8" cy="8" r="7.5" fill="var(--blue)"/><path d="M4 5c2 0 3 1 3 3s-2 2-2 4M10 3c0 2 2 2 3 3" stroke="var(--white)" stroke-width="1.5" fill="none"/></svg>
      www.INVEXCORP.com
    </div>
  </footer>
  <div class="color-bar"></div>
  <div class="page-number">5</div>
</div>
</body>
</html>
```